DRONE FLYERS.: : Presentation of the Corvale Aviation Drone Division Corvale Aviations has ...

- 1-Service to mining companies•Volumetric/Photogrammetry• Geophysical surveys•Mapping•Inspections-2- Visual and / or thermal inspections• Power lines•Pipelines/pipelines• Railroads-3- Services to municipalities•Planning• Various inspections• Civil security-4- Agricultural -55service•Multispectral•Mapping•Volumetric/Photogrammetry

```html
<!DOCTYPE html>
<html lang="fr">
<head>
<meta charset="utf-8">
<title>Corvale Aviation – Division Drones</title>
<link href="https://fonts.googleapis.com/css2?family=Oswald:wght@500&family=Roboto+Condensed:wght@400;700&family=Source+Sans+3:wght@300;400;600&display=swap" rel="stylesheet">
<style>
:root{
  --page:#d4d5d7;
  --dark:#2a2a2d;
  --dark-2:#3b3b3f;
  --white:#ffffff;
  --ink:#1f1f22;
  --blue:#5f9bd6;
  --blue-light:#c7d8ea;
  --grey-text:#444;
  --photo-a:#8b9198;
  --photo-b:#c3c7cc;
}
*{box-sizing:border-box;margin:0;padding:0}
html,body{width:849px;height:1200px;overflow:hidden;background:var(--page)}
body{position:relative;font-family:"Source Sans 3",sans-serif;color:var(--ink)}
.sheet{position:absolute;left:62px;width:738px;height:521px;overflow:hidden;background:var(--dark);box-shadow:0 6px 14px rgba(0,0,0,.25)}
.sheet--outside{top:52px}
.sheet--inside{top:622px}
.sheet__bg{position:absolute;inset:0}
.panel{position:absolute;top:0;width:246px;height:521px}
.panel--1{left:0}.panel--2{left:246px}.panel--3{left:492px}
.heading{font-family:"Oswald",sans-serif;font-weight:500;font-size:13px;letter-spacing:-.2px;text-transform:uppercase;position:absolute}
.heading--dark{color:var(--ink)}
.heading--light{color:var(--white)}
.rule{position:absolute;height:1px;background:var(--blue)}
.photo{position:absolute;background:linear-gradient(135deg,var(--photo-b),var(--photo-a));}
/* service list */
.service-list{position:absolute;left:23px;top:51px;list-style:none}
.service-list li{display:flex;align-items:center;height:24.5px;font-family:"Roboto Condensed",sans-serif;font-size:10px;color:var(--ink);text-transform:uppercase}
.service-list li svg{width:17px;height:17px;margin-right:7px;flex:none}
.mining-title{position:absolute;left:20px;top:424px;font-family:"Oswald",sans-serif;font-size:8px;color:var(--white);text-transform:uppercase;letter-spacing:-.2px}
.mini-list{position:absolute;top:443px;list-style:none;font-size:6.6px;color:var(--white);line-height:9.8px}
.mini-list li::before{content:"";display:inline-block;width:4px;height:4px;border-radius:50%;background:var(--blue);margin-right:4px;vertical-align:1px}
.intro{position:absolute;left:17px;top:166px;width:212px;font-size:8.3px;line-height:11.3px;color:#e9e9ea;text-align:justify}
.contact{position:absolute;left:0;width:246px;top:418px;text-align:center;font-size:7.4px;line-height:10px;color:var(--white)}
.contact strong{font-weight:600}
.brand{position:absolute;left:20px;top:24px;display:flex;align-items:center;color:var(--ink);font-weight:300}
.brand__mark{width:36px;height:36px;border-radius:50%;border:1.5px solid var(--ink);margin-right:14px}
.brand__name{font-size:10px;letter-spacing:1.6px;line-height:12px}
.brand__div{font-size:20px;line-height:22px}
.tagline{position:absolute;left:0;width:246px;top:432px;text-align:center;font-family:"Oswald",sans-serif;font-weight:500;font-size:12px;line-height:20px;color:var(--white);text-transform:uppercase;letter-spacing:-.2px}
.url-pill{position:absolute;left:18px;top:483px;width:216px;height:21px;border-radius:11px;background:var(--white);font-size:10.5px;line-height:21px;text-align:center;color:var(--ink)}
/* inside */
.caption{position:absolute;font-size:9px;line-height:12px}
.bullets{position:absolute;left:19px;top:173px;width:226px;list-style:none;font-size:8.7px;line-height:15.8px;color:#ececec}
.bullets li{padding-left:12px;position:relative}
.bullets li::before{content:"";position:absolute;left:0;top:5px;width:6px;height:6px;border-radius:50%;background:var(--blue)}
.benefits{position:absolute;left:17px;top:209px;list-style:none}
.benefits li{display:flex;align-items:center;height:31.5px;font-family:"Roboto Condensed",sans-serif;font-size:9.3px;color:#333;text-transform:uppercase}
.benefits li svg{width:28px;height:28px;margin-right:9px}
.bluebar{position:absolute;left:246px;top:481px;width:492px;height:20px;background:var(--blue);color:var(--white);font-size:11px;line-height:20px;display:flex}
.bluebar span{width:246px;text-align:center;display:flex;align-items:center;justify-content:center;gap:6px}
.feature{position:absolute;width:80px;text-align:center;font-family:"Roboto Condensed",sans-serif;font-size:8.6px;line-height:10.5px;color:var(--white);text-transform:uppercase}
.feature svg{display:block;margin:0 auto 5px;width:28px;height:28px}
</style>
</head>
<body>

<section class="sheet sheet--outside">
  <svg class="sheet__bg" viewBox="0 0 738 521" width="738" height="521">
    <defs>
      <linearGradient id="midGrad" x1="0" y1="0" x2="0" y2="1">
        <stop offset="0" stop-color="#e6e6e8"/><stop offset=".28" stop-color="#6a6a6e"/><stop offset=".6" stop-color="#333336"/><stop offset="1" stop-color="#2a2a2d"/>
      </linearGradient>
      <linearGradient id="whiteGrad" x1="0" y1="0" x2="1" y2="0">
        <stop offset="0" stop-color="#ffffff"/><stop offset="1" stop-color="#ececee"/>
      </linearGradient>
      <linearGradient id="photoGrad" x1="0" y1="0" x2="1" y2="1">
        <stop offset="0" stop-color="#c2c9d1"/><stop offset=".6" stop-color="#7d848c"/><stop offset="1" stop-color="#4a4f55"/>
      </linearGradient>
    </defs>
    <rect width="738" height="521" fill="#2a2a2d"/>
    <path d="M0 0H246V300C170 296 90 318 0 345Z" fill="url(#whiteGrad)"/>
    <path d="M0 345C90 318 170 296 246 300V312C170 308 90 330 0 358Z" fill="var(--blue)"/>
    <path d="M0 358C90 330 170 308 246 312V318C170 315 90 338 0 366Z" fill="#d9dde2"/>
    <rect x="246" width="246" height="521" fill="url(#midGrad)"/>
    <path d="M492 0H738V300C680 340 600 372 492 376Z" fill="url(#whiteGrad)"/>
    <path d="M492 110C560 85 650 70 738 66V300C680 340 600 372 492 376Z" fill="url(#photoGrad)" role="img" aria-label="Photo d'un drone quadrirotor posé au sol devant un bâtiment"/>
    <path d="M246 318C330 330 420 360 492 372C600 372 680 340 738 300V312C680 352 600 386 492 386C420 374 330 344 246 330Z" fill="var(--blue)"/>
    <path d="M246 330C330 344 420 374 492 386C600 386 680 352 738 312V322C680 362 600 396 492 396C420 384 330 354 246 340Z" fill="#d9dde2"/>
    <path d="M246 340C330 354 420 384 492 396C600 396 680 362 738 322V521H246Z" fill="#2a2a2d"/>
    <rect x="246" y="0" width="0.6" height="521" fill="#000" opacity=".15"/>
    <rect x="492" y="0" width="0.6" height="521" fill="#000" opacity=".15"/>
  </svg>

  <div class="panel panel--1">
    <h2 class="heading heading--dark" style="left:20px;top:26px">Service</h2>
    <div class="rule" style="left:20px;top:47px;width:115px;background:#9a9a9a"></div>
    <ul class="service-list">
      <li><svg viewBox="0 0 20 20"><circle cx="10" cy="10" r="10" fill="var(--blue)"/><rect x="5" y="7" width="10" height="7" rx="1" fill="#fff"/><circle cx="10" cy="10.5" r="2" fill="var(--blue)"/></svg>Photogrammétrie</li>
      <li><svg viewBox="0 0 20 20"><circle cx="10" cy="10" r="10" fill="var(--blue)"/><path d="M5 6h10v9H5z" fill="none" stroke="#fff" stroke-width="1.5"/></svg>Volumétrie</li>
      <li><svg viewBox="0 0 20 20"><circle cx="10" cy="10" r="10" fill="var(--blue)"/><circle cx="10" cy="7.5" r="2.5" fill="#fff"/><path d="M5 15c1-3 9-3 10 0z" fill="#fff"/></svg>Inspection</li>
      <li><svg viewBox="0 0 20 20"><circle cx="10" cy="10" r="10" fill="var(--blue)"/><path d="M10 4a3 3 0 0 1 3 3c0 2-3 5-3 5s-3-3-3-5a3 3 0 0 1 3-3zM5 15h10" stroke="#fff" stroke-width="1.5" fill="none"/></svg>Cartograhhie</li>
      <li><svg viewBox="0 0 20 20"><circle cx="10" cy="10" r="10" fill="var(--blue)"/><rect x="7" y="4" width="6" height="12" rx="1" fill="none" stroke="#fff" stroke-width="1.5"/></svg>Pente &amp; courbe de niveau</li>
      <li><svg viewBox="0 0 20 20"><circle cx="10" cy="10" r="10" fill="var(--blue)"/><path d="M8 6l6 4-6 4z" fill="#fff"/></svg>Plan 3D</li>
      <li><svg viewBox="0 0 20 20"><circle cx="10" cy="10" r="10" fill="var(--blue)"/><rect x="6" y="5" width="8" height="10" rx="1" fill="none" stroke="#fff" stroke-width="1.5"/><path d="M8 9h4M8 12h4" stroke="#fff"/></svg>Inspection thermique</li>
      <li><svg viewBox="0 0 20 20"><circle cx="10" cy="10" r="10" fill="var(--blue)"/><g fill="none" stroke="#fff" stroke-width="1.3"><circle cx="6.5" cy="6.5" r="2"/><circle cx="13.5" cy="6.5" r="2"/><circle cx="6.5" cy="13.5" r="2"/><circle cx="13.5" cy="13.5" r="2"/></g></svg>Suivit de projet</li>
      <li><svg viewBox="0 0 20 20"><circle cx="10" cy="10" r="10" fill="var(--blue)"/><rect x="4.5" y="7" width="8" height="6" fill="#fff"/><path d="M12.5 10l3.5-2.5v5z" fill="#fff"/></svg>Photographie aérienne / vidéographie</li>
    </ul>
    <div class="photo" style="left:11px;top:279px;width:136px;height:136px;border-radius:50%;border:6px solid var(--blue-light);background:radial-gradient(circle at 50% 50%,#c0a27a,#a7a9a6 55%,#8d918f)" role="img" aria-label="Vue aérienne d'un tas de matériaux sur un site minier"></div>
    <p class="mining-title">Service aux compagnies minières</p>
    <ul class="mini-list" style="left:21px">
      <li>Geophysical surveys</li><li>Mapping</li><li>Inspections Visual / thermal</li><li>Power lines</li><li>Pipelines/pipelines</li><li>Railroads</li>
    </ul>
    <ul class="mini-list" style="left:136px">
      <li>Services to municipalities</li><li>Planning</li><li>Civil security</li><li>Agricultural</li><li>Mapping</li><li>Volumetric/Photogrammetry</li>
    </ul>
  </div>

  <div class="panel panel--2">
    <div class="photo" style="left:70px;top:6px;width:118px;height:100px;background:radial-gradient(ellipse at 50% 55%,#4a4a4e,#9b9ca0 60%,rgba(200,200,204,0) 72%)" role="img" aria-label="Photo d'un drone en vol, vu de face"></div>
    <h2 class="heading heading--light" style="left:0;width:246px;text-align:center;top:132px">Division Drones</h2>
    <p class="intro">Comme nos pilotes de drone sont aussi nos pilotes d'hélicoptères, nous sommes en mesure de vous offrir une multitude de services dans plusieurs secteurs et ce, même en région éloignée! Tout nos pilotes possèdent leur certification avancée de l'Autorité Aérienne Nordique ainsi qu'une vaste expérience de vol. Nos équipements sont certifiés par l'Autorité Aérienne Nordique et nous pouvons opérer dans tous les espaces aériens. De jour comme de nuit, nous vous offrons des solutions adaptées à vos besoins avec une planification et un traitement de données rapides et à la fine pointe.</p>
    <h2 class="heading heading--light" style="left:0;width:246px;text-align:center;top:386px">Contact</h2>
    <p class="contact">La base principale des Corvale Aviations<br>Ltée est située à l'aéroport de Norvik, Québec (Canada).<br>GPS: 47°12'10"N 70°41'22"W<br><br><strong>Courriel: info@corvaleaviation.com<br>Téléphone: 555-014-3046<br>Fax: 555-014-0654</strong></p>
  </div>

  <div class="panel panel--3">
    <div class="brand">
      <span class="brand__mark"></span>
      <div><div class="brand__name">Corvale Aviation</div><div class="brand__div">Division Drones</div></div>
    </div>
    <p class="tagline">Photography, videography<br>&amp; drone inspection service</p>
    <div class="url-pill">www.corvaleaviation.com</div>
  </div>
</section>

<section class="sheet sheet--inside">
  <svg class="sheet__bg" viewBox="0 0 738 521" width="738" height="521">
    <defs>
      <linearGradient id="lakeGrad" x1="0" y1="0" x2="0" y2="1">
        <stop offset="0" stop-color="#5f6a4c"/><stop offset=".45" stop-color="#8a8f86"/><stop offset="1" stop-color="#b86f2f"/>
      </linearGradient>
      <linearGradient id="heliGrad" x1="0" y1="0" x2="0" y2="1">
        <stop offset="0" stop-color="#9fb0c2"/><stop offset=".6" stop-color="#c9a43a"/><stop offset="1" stop-color="#4d4a3f"/>
      </linearGradient>
      <linearGradient id="darkGrad" x1="0" y1="0" x2="0" y2="1">
        <stop offset="0" stop-color="#262628"/><stop offset="1" stop-color="#3a3a3e"/>
      </linearGradient>
    </defs>
    <rect width="738" height="521" fill="url(#darkGrad)"/>
    <path d="M0 380C60 372 120 360 246 352V521H0Z" fill="url(#heliGrad)" role="img" aria-label="Photo d'un hélicoptère jaune au sol et d'un drone en vol"/>
    <rect x="246" width="246" height="521" fill="#ffffff"/>
    <path d="M492 0H738V160C680 186 600 196 492 198Z" fill="url(#lakeGrad)" role="img" aria-label="Photo d'un hélicoptère rouge posé au bord d'un lac et d'un drone en vol"/>
    <path d="M492 198C600 196 680 186 738 160V167C680 194 600 205 492 206Z" fill="var(--blue)"/>
    <rect x="246" y="0" width="0.6" height="521" fill="#000" opacity=".12"/>
    <rect x="492" y="0" width="0.6" height="521" fill="#000" opacity=".12"/>
  </svg>

  <div class="panel panel--1">
    <h2 class="heading heading--light" style="left:19px;top:24px">Photogrammétrie</h2>
    <div class="rule" style="left:19px;top:47px;width:120px"></div>
    <div class="photo" style="left:19px;top:60px;width:104px;height:67px;border:1px solid #fff;background:linear-gradient(135deg,#8fa07d,#b9bcc0 55%,#6d7680)" role="img" aria-label="Vue aérienne orthogonale d'un chantier"></div>
    <div class="photo" style="left:130px;top:60px;width:104px;height:67px;border:1px solid #fff;background:linear-gradient(135deg,#8fa07d,#b9bcc0 55%,#6d7680)" role="img" aria-label="Vue aérienne oblique du même chantier"></div>
    <p class="caption" style="left:19px;top:146px;color:#f0f0f0">Création de cartes à partir de photos aériennes</p>
    <ul class="bullets">
      <li>Données d'inspection précises au centimètre près</li>
      <li>Plus rapide que les techniques traditionnelles</li>
      <li>Accès à des zones inaccessibles ou dangereuses pour l'homme</li>
      <li>Compilation de modèles numériques d'élévation, de contours, de mesures de volume, etc…</li>
    </ul>
    <div class="photo" style="left:6px;top:278px;width:96px;height:96px;border-radius:50%;border:5px solid var(--blue-light);background:radial-gradient(circle,#b8b4a8,#7b8a70)" role="img" aria-label="Vue aérienne d'une carrière"></div>
  </div>

  <div class="panel panel--2">
    <h2 class="heading heading--dark" style="left:0;width:246px;text-align:center;top:24px">Volumétrie</h2>
    <div class="rule" style="left:64px;top:47px;width:118px"></div>
    <div class="photo" style="left:16px;top:74px;width:217px;height:87px;background:linear-gradient(90deg,#fff 0 42%,#a6a69f 42%,#c8b08c 70%,#9c9e9a)" role="img" aria-label="Capture d'un calcul de volume sur une vue aérienne d'un tas de matériaux"></div>
    <p class="caption" style="left:16px;top:175px;width:217px;color:var(--grey-text);text-align:justify">Calcul volumétrique de matériaux divers à partir de photos aériennes</p>
    <ul class="benefits">
      <li><svg viewBox="0 0 28 28"><circle cx="14" cy="14" r="14" fill="#dfe9f5"/><circle cx="14" cy="14" r="10" fill="var(--blue)"/><circle cx="14" cy="14" r="5" fill="none" stroke="#fff" stroke-width="1.5"/><circle cx="14" cy="14" r="1.5" fill="#fff"/></svg>Précision</li>
      <li><svg viewBox="0 0 28 28"><circle cx="14" cy="14" r="14" fill="#dfe9f5"/><circle cx="14" cy="14" r="10" fill="var(--blue)"/><path d="M9 13h3v6H9zM13 19v-6l3-4c1 0 1.5 1 1 2l-.5 2H19v5z" fill="#fff"/></svg>Économie</li>
      <li><svg viewBox="0 0 28 28"><circle cx="14" cy="14" r="14" fill="#dfe9f5"/><circle cx="14" cy="14" r="10" fill="var(--blue)"/><circle cx="14" cy="15" r="5" fill="none" stroke="#fff" stroke-width="1.5"/><path d="M14 15V12M13 9h2" stroke="#fff" stroke-width="1.5"/></svg>Rapidité d'exécution</li>
      <li><svg viewBox="0 0 28 28"><circle cx="14" cy="14" r="14" fill="#dfe9f5"/><circle cx="14" cy="14" r="10" fill="var(--blue)"/><rect x="10.5" y="13" width="7" height="6" rx="1" fill="#fff"/><path d="M12 13v-2a2 2 0 0 1 4 0v2" fill="none" stroke="#fff" stroke-width="1.4"/></svg>Sécurité</li>
    </ul>
    <div class="photo" style="left:7px;top:354px;width:232px;height:102px;background:linear-gradient(90deg,#f4f4f4 0 27%,#b0aca0 27% 73%,#f4f4f4 73%)" role="img" aria-label="Capture de mesures et profil d'élévation d'un tas de matériaux"></div>
  </div>

  <div class="panel panel--3">
    <h2 class="heading heading--light" style="left:20px;top:202px">Inspection</h2>
    <div class="rule" style="left:20px;top:225px;width:120px"></div>
    <p class="caption" style="left:20px;top:230px;color:#f0f0f0">Visuelle ou Thermique</p>
    <div class="feature" style="left:7px;top:264px"><svg viewBox="0 0 28 28"><circle cx="14" cy="14" r="13" fill="none" stroke="#fff" stroke-width="1.2"/><circle cx="14" cy="14" r="9" fill="var(--blue)"/><path d="M9 16a5 5 0 0 1 10 0M14 16l3-3" stroke="#fff" stroke-width="1.4" fill="none"/></svg>Rapidité</div>
    <div class="feature" style="left:81px;top:264px"><svg viewBox="0 0 28 28"><circle cx="14" cy="14" r="13" fill="none" stroke="#fff" stroke-width="1.2"/><circle cx="14" cy="14" r="9" fill="var(--blue)"/><circle cx="14" cy="14" r="4.5" fill="none" stroke="#fff" stroke-width="1.4"/><circle cx="14" cy="14" r="1.3" fill="#fff"/></svg>Précision</div>
    <div class="feature" style="left:156px;top:264px"><svg viewBox="0 0 28 28"><circle cx="14" cy="14" r="13" fill="none" stroke="#fff" stroke-width="1.2"/><circle cx="14" cy="14" r="9" fill="var(--blue)"/><path d="M10 10l8 8M18 10l-8 8" stroke="#fff" stroke-width="1.4"/></svg>Accès difficile</div>
    <div class="feature" style="left:47px;top:317px"><svg viewBox="0 0 28 28"><circle cx="14" cy="14" r="13" fill="none" stroke="#fff" stroke-width="1.2"/><circle cx="14" cy="14" r="9" fill="var(--blue)"/><path d="M14 8.5l5.5 9.5h-11z" fill="#fff"/><path d="M14 12v3" stroke="var(--blue)" stroke-width="1.3"/></svg>Zones<br>dangereuses</div>
    <div class="feature" style="left:123px;top:317px"><svg viewBox="0 0 28 28"><circle cx="14" cy="14" r="13" fill="none" stroke="#fff" stroke-width="1.2"/><circle cx="14" cy="14" r="9" fill="var(--blue)"/><path d="M8.5 17a5.5 5.5 0 0 1 11 0z" fill="#fff"/><path d="M7.5 17.5h13" stroke="#fff" stroke-width="1.4"/></svg>Suivi de<br>chantier</div>
    <div class="photo" style="left:18px;top:397px;width:105px;height:67px;border:1px solid #fff;background:linear-gradient(135deg,#3d3f55,#c0572f 45%,#e7c15a 60%,#6b6d72)" role="img" aria-label="Écran de caméra thermique montrant une inspection"></div>
    <div class="photo" style="left:129px;top:397px;width:104px;height:67px;border:1px solid #fff;background:linear-gradient(135deg,#9aa49a,#c4c1b8 55%,#6f7d86)" role="img" aria-label="Vue aérienne d'un chantier industriel"></div>
  </div>

  <div class="bluebar">
    <span><svg width="11" height="11" viewBox="0 0 12 12"><circle cx="6" cy="6" r="5.3" fill="none" stroke="#fff"/><path d="M4 3.2l1 1.4-.6.8c.4.9 1 1.5 1.9 1.9l.8-.6 1.4 1-.6 1c-2.4-.3-4.3-2.2-4.6-4.6z" fill="#fff"/></svg>555-014-0654</span>
    <span>www.corvaleaviation.com</span>
  </div>
</section>

</body>
</html>
```